KRWB new business card design

We need a business card design for our established business which is Australia wide however based in Melbourne. We are a young team of Financial Planners who specialize in Insurance and Basic super advice for people like us.

We are people who help our clients get things done in a timely and cost effective manner whilst having a good time and a laugh along the way.

We would like this to have a consistent feel with our new e-brochure which i have attached from a color and font perspective.

Industry/Entity Type

Business

Requirements
Must have
• We do not need specific address details rather just the states we are in:

VIC/NSW/QLD/TAS
Nice to have
• Curved edge to mate the brochure

```html
<!DOCTYPE html>
<html lang="en">
<head>
<meta charset="utf-8">
<title>KRWB business card</title>
<link rel="stylesheet" href="https://fonts.googleapis.com/css2?family=Arimo:ital,wght@0,400;0,700;1,700&family=Didact+Gothic&family=PT+Sans&display=swap">
<style>
  :root {
    --stage: #7a4f30;
    --card-white: #ffffff;
    --green-light: #6cc04a;
    --green-dark: #12a54c;
    --green-faint: #eef4ec;
    --ink: #1c1c1c;
    --ink-soft: #3c3c3c;
    --grey: #767676;
    --carbon-top: #2a2a2a;
    --carbon-bottom: #111111;
    --label: #1a1a1a;
  }
  * { margin: 0; padding: 0; box-sizing: border-box; }
  html, body { width: 1200px; height: 788px; overflow: hidden; }
  body { background: var(--stage); position: relative; font-family: "Arimo", Arial, sans-serif; }

  .view-label {
    position: absolute; width: 525px; text-align: center;
    font-family: "PT Sans", sans-serif; font-size: 21px; color: var(--label);
  }
  .card {
    position: absolute; width: 525px; height: 300px; border-radius: 22px;
    background: var(--card-white); overflow: hidden;
  }

  /* brand lockup */
  .brand { position: absolute; display: flex; align-items: center; gap: 10px; }
  .brand-mark { background: var(--green-light); }
  .brand-name { font-family: "Arimo", sans-serif; font-weight: 700; letter-spacing: 1px; }

  /* front */
  .front .brand { left: 0; right: 0; top: 62px; justify-content: center; }
  .front .brand-mark { width: 34px; height: 34px; }
  .front .brand-name { font-size: 44px; color: var(--ink); }
  .front-band { position: absolute; left: 0; top: 154px; width: 525px; height: 75px; }
  .holder { position: absolute; left: 27px; top: 162px; color: #fff; font-weight: 700; }
  .holder-name { font-size: 18px; line-height: 22px; }
  .holder-meta { font-size: 13.5px; line-height: 20px; }
  .online { position: absolute; right: 34px; top: 173px; color: #fff; text-align: right;
    font-family: "Didact Gothic", sans-serif; font-size: 13.5px; line-height: 19px; }
  .online b { font-family: "Arimo", sans-serif; font-style: italic; }
  .contact { position: absolute; left: 0; right: 0; top: 245px; text-align: center;
    font-family: "Didact Gothic", sans-serif; font-size: 14px; line-height: 25px; color: var(--ink-soft); }
  .contact b { font-family: "Arimo", sans-serif; font-style: italic; font-weight: 700; }
  .contact .sep { padding: 0 6px; }

  /* services list */
  .services { position: absolute; list-style: none; font-weight: 700; font-size: 14px; }
  .services-title { font-style: italic; font-size: 18px; margin-bottom: 13px; }
  .services li { line-height: 34px; }
  .services li::before { content: "\25AA"; margin-right: 5px; font-size: 11px; vertical-align: 1px; }

  /* back 1 */
  .back-one .brand { left: 0; width: 260px; top: 110px; justify-content: center; }
  .back-one .brand-mark { width: 30px; height: 30px; }
  .back-one .brand-name { font-size: 40px; color: var(--ink); }
  .divider { position: absolute; left: 259px; top: 20px; width: 3px; height: 238px;
    background: linear-gradient(to bottom, transparent, #9a9a9a 50%, transparent); }
  .back-one .services { left: 319px; top: 44px; color: var(--grey); }
  .back-one .services-title { margin-left: 0; }
  .back-one .services li { line-height: 34px; }
  .tagline-band { position: absolute; left: 0; bottom: 0; width: 100%; height: 39px;
    background: var(--green-light); color: #fff; font-weight: 700; font-size: 14px;
    text-align: center; line-height: 37px; }

  /* back 2 */
  .faint-name { position: absolute; left: 0; right: 0; top: 68px; text-align: center;
    font-weight: 700; font-size: 120px; color: var(--green-faint); letter-spacing: 4px; }
  .back-two .services { left: 0; right: 0; top: 45px; text-align: center; color: var(--ink-soft); }
  .back-two .tagline { position: absolute; left: 0; right: 0; bottom: 17px; text-align: center;
    font-weight: 700; font-size: 14px; color: var(--ink-soft); }

  /* back 3 */
  .back-three { background: var(--carbon-bottom); }
  .carbon { position: absolute; inset: 0; background: linear-gradient(160deg, var(--carbon-top), var(--carbon-bottom)); }
  .back-three .brand { left: 40px; top: 110px; }
  .back-three .brand-mark { width: 44px; height: 44px; }
  .back-three .brand-name { font-size: 62px; color: #fff; }
  .back-three .services { left: 314px; top: 25px; color: #fff; }
  .back-three .tagline { position: absolute; left: 313px; top: 253px; font-weight: 700; font-size: 14px;
    line-height: 18px; color: var(--green-light); }
</style>
</head>
<body>
  <div class="view-label" style="left:53px;top:33px;">Front</div>
  <div class="view-label" style="left:622px;top:33px;">Back - 1</div>
  <div class="view-label" style="left:53px;top:403px;">Back - 2</div>
  <div class="view-label" style="left:622px;top:403px;">Back - 3</div>

  <section class="card front" style="left:53px;top:72px;">
    <div class="brand"><span class="brand-mark"></span><span class="brand-name">KRWB</span></div>
    <svg class="front-band" viewBox="0 0 525 75" aria-hidden="true">
      <polygon points="0,0 240,0 186,75 0,75" fill="var(--green-light)"/>
      <polygon points="252,0 525,0 525,75 198,75" fill="var(--green-dark)"/>
    </svg>
    <div class="holder">
      <div class="holder-name">Daniel Hartley</div>
      <div class="holder-meta">ADFS, BBus, LRS©</div>
      <div class="holder-meta">Financial Adviser</div>
    </div>
    <div class="online">
      <div><b>email</b> daniel@krwb.com.au</div>
      <div><b>web</b> www.krwb.com.au</div>
    </div>
    <div class="contact">
      <div><b>cell</b> 0400 555 218<span class="sep">|</span><b>phone</b> 1300 555 742</div>
      <div><b>fax</b> 03 9555 0184<span class="sep">|</span>VIC/NSW/QLD/TAS</div>
    </div>
  </section>

  <section class="card back-one" style="left:622px;top:74px;">
    <div class="brand"><span class="brand-mark"></span><span class="brand-name">KRWB</span></div>
    <div class="divider"></div>
    <ul class="services">
      <li class="services-title" style="list-style:none;">Specialising in</li>
      <li>Risk Insurance</li>
      <li>Debt Management</li>
      <li>Superannuation</li>
      <li>Wealth Creation</li>
      <li>Retirement Planning</li>
    </ul>
    <div class="tagline-band">SECURE FUTURE, ENHANCED LIFESTYLE</div>
  </section>

  <section class="card back-two" style="left:53px;top:445px;">
    <div class="faint-name" aria-hidden="true">KRWB</div>
    <ul class="services">
      <li class="services-title">Specialising in</li>
      <li>Risk Insurance</li>
      <li>Debt Management</li>
      <li>Superannuation</li>
      <li>Wealth Creation</li>
      <li>Retirement Planning</li>
    </ul>
    <div class="tagline">SECURE FUTURE, ENHANCED LIFESTYLE</div>
  </section>

  <section class="card back-three" style="left:622px;top:445px;">
    <div class="carbon" role="img" aria-label="Dark carbon-fibre mesh texture"></div>
    <div class="brand"><span class="brand-mark"></span><span class="brand-name">KRWB</span></div>
    <ul class="services">
      <li class="services-title">Specialising in</li>
      <li>Risk Insurance</li>
      <li>Debt Management</li>
      <li>Superannuation</li>
      <li>Wealth Creation</li>
      <li>Retirement Planning</li>
    </ul>
    <div class="tagline">SECURE FUTURE<br>ENHANCED LIFESTYLE</div>
  </section>
</body>
</html>
```